Industrial Project Sign

We need an eye catching (but professional) industrial project sign that will be very large (roughly 12' high x 18' wide). This sign will be highly visible from the adjacent high speed highway.

* The following needs to be at the bottom of the signage: Logo (uploaded), Name (Brightline Property Partners, Inc.) (uploaded) and phone number (415)736-2958

*Name of Project - "Meridale Commerce Park"

* Text items
Land for Sale
Build to Suit
Zoning: Industrial (G I & L I)

* Interesting background that is eye catching
Updates

Good morning all,

We are considering all designers options as we go and are waiting for the final designs to come in by the 4th so that we can give each one a good look.   If you have any new designs, questions, further design options or any tweeks you want to do to current designs, please do so at this time.

Thanks to all of you for your submissions.

Industry/Entity Type

Industrial

```html
<!DOCTYPE html>
<html lang="en">
<head>
<meta charset="utf-8">
<title>Land For Sale – Industrial Project Sign</title>
<link rel="stylesheet" href="https://fonts.googleapis.com/css2?family=Oswald:wght@700&family=Arimo:wght@700&display=swap">
<style>
  :root {
    --maroon: #5a0a0c;
    --white: #ffffff;
    --frame: #3a3a3a;
  }
  html, body {
    margin: 0;
    padding: 0;
    width: 1200px;
    height: 1000px;
    overflow: hidden;
    background: var(--white);
  }
  .canvas {
    position: relative;
    width: 1200px;
    height: 1000px;
    box-sizing: border-box;
    border: 1px solid var(--frame);
    background: var(--white);
  }
  .canvas svg { position: absolute; top: 0; left: 0; }
  .headline { font-family: "Oswald", "Arial Narrow", sans-serif; font-weight: 700; }
  .detail { font-family: "Arimo", Arial, sans-serif; font-weight: 700; }
  .fill-maroon { fill: var(--maroon); }
  .fill-white { fill: var(--white); }
</style>
</head>
<body>
<div class="canvas">
  <svg width="1200" height="1000" viewBox="0 0 1200 1000" xmlns="http://www.w3.org/2000/svg">
    <defs>
      <symbol id="project-sign" viewBox="0 0 892 596">
        <rect class="fill-maroon" x="0" y="0" width="892" height="596"/>
        <ellipse class="sign-oval fill-white" cx="446" cy="142" rx="446" ry="107"/>
        <text class="headline fill-maroon" x="65" y="199" font-size="142" textLength="765" lengthAdjust="spacingAndGlyphs">LAND FOR SALE</text>
        <text class="headline fill-white" x="90" y="384" font-size="128" textLength="715" lengthAdjust="spacingAndGlyphs">BUILD TO SUIT</text>
        <text class="detail fill-white" x="60" y="449" font-size="46" textLength="770" lengthAdjust="spacingAndGlyphs">ZONING: INDUSTRIAL (G I &amp; L I)</text>
        <rect class="contact-band fill-white" x="1.5" y="494" width="889" height="100.5" stroke="var(--maroon)" stroke-width="3"/>
        <rect class="brand-mark fill-maroon" x="30" y="533" width="28" height="28"/>
        <text class="detail fill-maroon" x="68" y="554" font-size="20" textLength="385" lengthAdjust="spacingAndGlyphs">Brightline Property Partners, Inc.</text>
        <line class="band-divider" x1="461" y1="502" x2="461" y2="587" stroke="var(--maroon)" stroke-width="3"/>
        <text class="headline fill-maroon" x="477" y="564" font-size="46" textLength="388" lengthAdjust="spacingAndGlyphs">Phone :(415) 736-2958</text>
      </symbol>
    </defs>
    <use class="sign-large" href="#project-sign" x="155" y="46" width="892" height="596"/>
    <use class="sign-small" href="#project-sign" x="839" y="738" width="322" height="215"/>
  </svg>
</div>
</body>
</html>
```